Elegant Business Card with Logo and Picture

Please create a business card that has the Logo colors add Gold and turquoise / use the attached logo - I would like a beautiful Business Card - Please make sure it's printed on both sides / Picture can go on one side Logo other
www.velmoragrove.com
614-372-0583
Lina Suzette Brolin
linasb@quorvamail.com
Life Coach
Thessing Certified Teacher / Life Coach / Interior Designer
Transformational Retreats

Target Market(s)

Women Men General

Industry/Entity Type

Life Coaching

Contact Information for Business Card

www.velmoragrove.com
614-372-0583
Lina Suzette Brolin
Life Coach
Thessing Certified Teacher / Yoga Teacher / Interior Designer

Font styles to use
Serif
Decorative

Colors
33a6d6
e34197
ffc214

Requirements
Must have
• Quality Paper and touch /
Nice to have
• Beautiful Touch and feel
Should not have
• needs to be elegant

```html
<!DOCTYPE html>
<html lang="en">
<head>
<meta charset="utf-8">
<title>Velmora Grove Coaching – Business Card</title>
<link rel="stylesheet" href="https://fonts.googleapis.com/css2?family=Arvo&family=Roboto:wght@400;500;700&family=Roboto+Condensed:wght@400&display=swap">
<style>
  :root {
    --backdrop: #d9d9d9;
    --paper: #ffffff;
    --ink: #1a1a1a;
    --muted: #4a4a4a;
    --magenta: #e5157f;
    --charcoal: #232323;
    --charcoal-deep: #1b1b1b;
    --white: #ffffff;
    --photo-warm: #e9c7a6;
    --photo-hair: #e2c07e;
    --photo-stripe: #d9736b;
  }
  * { margin: 0; padding: 0; box-sizing: border-box; }
  html, body { width: 1200px; height: 1200px; overflow: hidden; }
  body { background: var(--backdrop); position: relative; }

  .card {
    position: absolute;
    left: 262px;
    width: 686px;
    height: 392px;
    border-radius: 22px;
    overflow: hidden;
  }
  .card--front { top: 165px; background: var(--paper); }
  .card--back { top: 653px; background: linear-gradient(180deg, var(--charcoal) 0%, var(--charcoal-deep) 100%); }

  /* front */
  .brand-mark {
    position: absolute;
    left: 42px;
    top: 58px;
    width: 257px;
    text-align: center;
  }
  .brand-mark__symbol {
    display: flex;
    align-items: center;
    justify-content: center;
    gap: 10px;
    font-family: "Arvo", serif;
    font-size: 30px;
    line-height: 36px;
    color: var(--ink);
  }
  .brand-mark__dot {
    width: 14px;
    height: 14px;
    border-radius: 50%;
    background: var(--magenta);
  }
  .brand-mark__name {
    margin-top: 37px;
    font-family: "Arvo", serif;
    font-size: 18px;
    line-height: 20px;
    letter-spacing: 2.5px;
    color: var(--ink);
    white-space: nowrap;
  }
  .brand-mark__sub {
    font-family: "Arvo", serif;
    font-size: 9px;
    line-height: 11px;
    letter-spacing: 10px;
    padding-left: 10px;
    color: var(--ink);
  }

  .person {
    position: absolute;
    left: 42px;
    top: 203px;
  }
  .person__name {
    font-family: "Roboto", sans-serif;
    font-weight: 700;
    font-size: 24px;
    color: var(--magenta);
    line-height: 28px;
  }
  .person__roles {
    margin-top: 6px;
    font-family: "Roboto Condensed", sans-serif;
    font-size: 15.5px;
    line-height: 19px;
    color: var(--ink);
  }
  .contact {
    list-style: none;
    margin-top: 11px;
    font-family: "Roboto", sans-serif;
    font-size: 15.5px;
    color: var(--muted);
  }
  .contact__item { display: flex; align-items: center; height: 19.5px; }
  .contact__icon { width: 13px; height: 13px; margin-right: 9px; flex: none; }

  .portrait {
    position: absolute;
    right: 0;
    top: 16px;
    width: 331px;
    height: 376px;
    background:
      radial-gradient(ellipse 42% 38% at 55% 38%, var(--photo-warm) 0%, rgba(233,199,166,0) 100%),
      radial-gradient(ellipse 55% 45% at 55% 35%, var(--photo-hair) 0%, rgba(226,192,126,0) 100%),
      linear-gradient(180deg, rgba(255,255,255,0) 70%, var(--photo-stripe) 100%);
  }

  /* back */
  .back-name {
    position: absolute;
    left: 290px;
    top: 150px;
    width: 370px;
    text-align: center;
    font-family: "Arvo", serif;
    font-size: 72px;
    line-height: 90px;
    color: var(--white);
  }
  .back-brand {
    position: absolute;
    left: 34px;
    top: 318px;
    font-family: "Arvo", serif;
    font-size: 16px;
    line-height: 18px;
    letter-spacing: 2px;
    color: var(--white);
    white-space: nowrap;
  }
  .back-brand__sub {
    display: block;
    font-size: 7px;
    line-height: 9px;
    letter-spacing: 9px;
    padding-left: 46px;
  }
  .back-web {
    position: absolute;
    left: 34px;
    top: 347px;
    font-family: "Roboto", sans-serif;
    font-size: 15.5px;
    letter-spacing: 1.4px;
    color: var(--white);
  }
</style>
</head>
<body>

<section class="card card--front" aria-label="Business card front">
  <div class="brand-mark">
    <div class="brand-mark__symbol"><span class="brand-mark__dot" aria-hidden="true"></span>Velmora</div>
    <div class="brand-mark__name">VELMORA GROVE</div>
    <div class="brand-mark__sub">COACHING</div>
  </div>

  <div class="person">
    <h1 class="person__name">Lina Suzette Brolin</h1>
    <p class="person__roles">Life Coach<br>Thessing Certified Teacher /<br>Yoga Teacher / Interior Designer</p>
    <ul class="contact">
      <li class="contact__item">
        <svg class="contact__icon" viewBox="0 0 16 16" aria-hidden="true"><path fill="#e5157f" d="M3.5 1l2.5 0.5 1 3.5-1.8 1.4a9 9 0 0 0 4.4 4.4L11 9l3.5 1 0.5 2.5-2 2.3C6.5 14.5 1.5 9.5 1.2 3z"/></svg>
        614-372-0583
      </li>
      <li class="contact__item">
        <svg class="contact__icon" viewBox="0 0 16 16" aria-hidden="true"><rect x="1" y="4" width="14" height="9" fill="#e5157f"/><path d="M1 4l7 5 7-5" fill="none" stroke="#fff" stroke-width="1.3"/></svg>
        linasb@quorvamail.com
      </li>
      <li class="contact__item">
        <svg class="contact__icon" viewBox="0 0 16 16" aria-hidden="true"><circle cx="8" cy="8" r="7" fill="#e5157f"/><path d="M4 5.5c2 0 2 2 3.5 2.5s0 3 1.5 4M9 2.5c0 2 2 2 3.5 2.5" fill="none" stroke="#fff" stroke-width="1.3"/></svg>
        www.velmoragrove.com
      </li>
    </ul>
  </div>

  <div class="portrait" role="img" aria-label="Portrait photo of Lina Suzette Brolin"></div>
</section>

<section class="card card--back" aria-label="Business card back">
  <div class="back-name">Velmora</div>
  <div class="back-brand">VELMORA GROVE<span class="back-brand__sub">COACHING</span></div>
  <div class="back-web">www.velmoragrove.com</div>
</section>

</body>
</html>
```